Tolvane Inc., a third party debt collection agency needs a Website

Tolvane needs a very basic website (3 basic pages) so that consumers can download forms, potential employees can get required EEO language and see potential jobs, and to show that they are a consumer friendly organization.

I've attached a list of requirements and wishes titled "Tolvane Website Specifications"

Target Market(s)

Consumers that need to repay their government loans; Tolvane will walk through the process to assist them.

Industry/Entity Type

Financial Service

Coding

Coded - Design and coding required

Number of Pages Required

1 page

Font styles to use
Sans Serif

Colors
0355a3

Requirements
Must have
• Tolvane Logo
• See document "Tolvane Website Specifications" for all requirements

```html
<!DOCTYPE html>
<html lang="en">
<head>
<meta charset="utf-8">
<title>Tolvane Inc. — Third Party Debt Collection</title>
<link rel="stylesheet" href="https://fonts.googleapis.com/css2?family=Open+Sans:wght@400;600&family=Raleway:wght@400;500;600&display=swap">
<style>
  :root {
    --navy: #2b2a72;
    --navy-deep: #1f1e5c;
    --brand-red: #8b1c22;
    --text-grey: #666a70;
    --band: #e6e9f3;
    --card: #4b4a98;
    --footer: #0f1419;
    --footer-bottom: #080b0e;
    --footer-text: #a9adb3;
    --white: #ffffff;
  }
  * { margin: 0; padding: 0; box-sizing: border-box; }
  html, body { width: 862px; height: 1200px; overflow: hidden; background: var(--white); }
  body { position: relative; font-family: "Open Sans", sans-serif; color: var(--text-grey); }

  .hero {
    position: absolute; left: 0; top: 0; width: 862px; height: 432px;
    background: linear-gradient(100deg, #f3f5f9 0%, #e9ecf3 38%, #8c93a8 62%, #3b3f55 80%, #2a2d3d 100%);
    border-bottom: 2px solid #d9dbe0;
  }
  .header {
    position: absolute; left: 0; top: 0; width: 862px; height: 86px;
    background: rgba(255,255,255,0.88);
  }
  .brand {
    position: absolute; left: 79px; top: 42px;
    display: flex; align-items: center; gap: 7px;
    font-family: "Raleway", sans-serif; font-weight: 600; font-size: 18px; color: var(--brand-red);
  }
  .brand-dot { width: 10px; height: 10px; border-radius: 50%; background: var(--navy); }
  .nav { position: absolute; top: 38px; left: 0; width: 862px; list-style: none; }
  .nav li {
    position: absolute; font-family: "Open Sans", sans-serif; font-size: 10px;
    color: #2c2c3a; letter-spacing: 0.2px;
  }
  .nav li.active { color: var(--navy); font-weight: 600; }
  .nav li.active::before {
    content: ""; position: absolute; left: 3px; top: -8px; width: 24px; height: 3px;
    border-radius: 2px; background: var(--navy);
  }
  .hero-title {
    position: absolute; left: 76px; top: 307px;
    font-family: "Raleway", sans-serif; font-weight: 500; font-size: 22px; color: var(--navy);
  }
  .slider-dots { position: absolute; left: 397px; top: 400px; display: flex; gap: 8px; }
  .slider-dots span { width: 11px; height: 11px; border: 1.5px solid #5a5a66; }
  .slider-dots span.current { background: #b4585e; border-color: #7a2a30; }

  .section-title {
    position: absolute; left: 0; width: 862px; text-align: center;
    font-family: "Raleway", sans-serif; font-weight: 400; font-size: 19px; color: #2a2a36;
  }
  .intro {
    position: absolute; left: 92px; top: 503px; width: 678px; text-align: center;
    font-size: 8.6px; line-height: 22px;
  }

  .services-band { position: absolute; left: 0; top: 640px; width: 862px; height: 156px; background: var(--band); }
  .service-card {
    position: absolute; top: 640px; height: 156px; padding: 38px 18px 0;
    background: linear-gradient(160deg, #5856a6 0%, var(--card) 55%, #3e3d86 100%);
    text-align: center; color: var(--white);
  }
  .service-card h3 { font-family: "Raleway", sans-serif; font-weight: 500; font-size: 14.5px; margin-bottom: 7px; }
  .service-card h3::after {
    content: ""; display: block; width: 52px; height: 2px; margin: 7px auto 0; background: var(--navy-deep);
  }
  .service-card p { font-size: 7.6px; line-height: 18.5px; }
  .services-shadow {
    position: absolute; left: 40px; top: 796px; width: 782px; height: 14px;
    background: radial-gradient(ellipse at top, rgba(0,0,0,0.16), rgba(0,0,0,0) 70%);
  }

  .feature-icon {
    position: absolute; top: 849px; width: 83px; height: 83px; border-radius: 50%;
    border: 1.5px solid var(--navy-deep); display: flex; align-items: center; justify-content: center;
  }
  .feature { position: absolute; top: 845px; width: 218px; }
  .feature h3 { font-family: "Raleway", sans-serif; font-weight: 400; font-size: 15px; color: #2a2a36; margin-bottom: 8px; }
  .feature p { font-size: 7.6px; line-height: 18.5px; text-align: justify; }
  .feature .more { display: block; margin-top: 7px; font-size: 10px; color: var(--brand-red); }
  .feature .more::before {
    content: ""; display: inline-block; margin-right: 4px; vertical-align: 1px;
    border-left: 4px solid var(--brand-red); border-top: 3px solid transparent; border-bottom: 3px solid transparent;
  }

  .footer { position: absolute; left: 0; top: 984px; width: 862px; height: 160px; background: var(--footer); color: var(--footer-text); }
  .footer h4 { position: absolute; font-family: "Raleway", sans-serif; font-weight: 500; font-size: 11.5px; color: var(--white); }
  .footer-divider { position: absolute; top: 22px; height: 106px; border-left: 1px dotted #2c323a; }
  .about-text { position: absolute; left: 80px; top: 50px; width: 222px; font-size: 7.6px; line-height: 19.7px; text-align: justify; }
  .contact-list { position: absolute; left: 360px; top: 48px; list-style: none; font-size: 7.8px; }
  .contact-list li { position: relative; padding-left: 18px; }
  .contact-list svg { position: absolute; left: 0; top: 1px; }
  .contact-list .org { color: var(--white); font-size: 9.5px; }
  .info-links { position: absolute; left: 546px; top: 45px; list-style: none; font-size: 7.8px; line-height: 22px; }
  .badge-a { position: absolute; left: 694px; top: 24px; width: 50px; height: 56px; background: #3b6fa8; opacity: 0.85; }
  .badge-b { position: absolute; left: 681px; top: 102px; width: 76px; height: 29px; border-radius: 5px; background: #1a5d86; }
  .footer-bottom { position: absolute; left: 0; top: 1144px; width: 862px; height: 56px; background: var(--footer-bottom); }
  .copyright { position: absolute; left: 80px; top: 24px; font-size: 7.8px; color: #c4c7cc; }
  .social { position: absolute; left: 729px; top: 22px; display: flex; gap: 4px; }
  .social span { width: 15px; height: 15px; border-radius: 50%; background: #3a78b8; }
</style>
</head>
<body>

<div class="hero" role="img" aria-label="Photo of two business colleagues smiling while reviewing a tablet at a bright office desk"></div>

<header class="header">
  <div class="brand"><span class="brand-dot"></span>Tolvane Inc.</div>
  <ul class="nav">
    <li class="active" style="left:362px">HOME</li>
    <li style="left:426px">SERVICES</li>
    <li style="left:503px">ABOUT US</li>
    <li style="left:585px">BLOG</li>
    <li style="left:646px">SUPPORT</li>
    <li style="left:723px">CONTACT US</li>
  </ul>
</header>

<h1 class="hero-title">THIRD PARTY DEBT COLLECTION</h1>
<div class="slider-dots"><span></span><span></span><span class="current"></span><span></span></div>

<h2 class="section-title" style="top:468px">WHO WE ARE?</h2>
<p class="intro">Tolvane is a third party debt collection agency that is focused on the collection of higher education loans. Tolvane is compliant with all federal, state, and local laws and is committed to the professional and fair treatment of consumers. Our goal is to assist consumers in resolving their obligations in the manner that best meets their needs and to provide information necessary in order for consumers to make an informed decision.</p>

<h2 class="section-title" style="top:598px">OUR SERVICES</h2>
<div class="services-band"></div>
<div class="service-card" style="left:79px;width:234px" role="img" aria-label="Service tile over a photo of a business meeting">
  <h3>LOREM IPSUM DOLOR</h3>
  <p>Aliquam commodo vulputate metus at laoreet. Sed tempor tincidunt scelerisque. Quisque porttitor di am velit, nec luctus metus laoreet at.</p>
</div>
<div class="service-card" style="left:315px;width:232px" role="img" aria-label="Service tile over a photo of hands working with documents">
  <h3>DONEC TINCIDUNT</h3>
  <p>Duis pellentesque nibh vulputate aliquam faucibu s. Aliquam commodo vulputate metus at laore et. Sed tempor tincidunt scelerisque.</p>
</div>
<div class="service-card" style="left:549px;width:232px" role="img" aria-label="Service tile over a photo of a team at a conference table">
  <h3>PRAESENT VIVERRA</h3>
  <p>Aliquam commodo vulputate metus at laoreet. Sed tempor tincidunt scelerisque. Quisque porttitor di am velit, nec luctus metus laoreet at.</p>
</div>
<div class="services-shadow"></div>

<div class="feature-icon" style="left:80px">
  <svg width="34" height="30" viewBox="0 0 34 30" fill="#2b2a72" aria-hidden="true">
    <circle cx="8" cy="7" r="4"/><circle cx="26" cy="7" r="4"/><circle cx="17" cy="9" r="5"/>
    <path d="M1 22c0-5 3-8 7-8s5 2 5 2v6z"/><path d="M33 22c0-5-3-8-7-8s-5 2-5 2v6z"/>
    <path d="M8 30v-6c0-5 4-9 9-9s9 4 9 9v6z"/>
  </svg>
</div>
<div class="feature" style="left:182px">
  <h3>CONSUMER INFORMATION</h3>
  <p>Lorem ipsum dolor sit amet, consectetur adipiscing elit. Morbi ex lorem, scelerisque ut vehicula ac, gravida id mauris. Etiam turpis augue.</p>
  <span class="more">MORE DETAILS</span>
</div>

<div class="feature-icon" style="left:455px">
  <svg width="26" height="32" viewBox="0 0 26 32" fill="none" stroke="#2b2a72" stroke-width="2" aria-hidden="true">
    <path d="M2 2h15l7 7v21H2z"/><path d="M17 2v7h7"/>
    <path d="M7 15h12M7 20h12M7 25h12"/>
  </svg>
</div>
<div class="feature" style="left:557px">
  <h3>CAREERS @ TOLVANE</h3>
  <p>Nulla placerat vel magna a cursus. Nulla mattis, elit phare-tra ultrices vehicula, lacus justo venenatis eros, eget pre-tium tortor odio sit amet diam.</p>
  <span class="more">MORE DETAILS</span>
</div>

<footer class="footer">
  <h4 style="left:80px;top:22px">ABOUT</h4>
  <p class="about-text">Tolvane is a third party debt collection agency that is focused on the collection of higher education loans. Tolvane is compliant with all federal, state, and local laws and is committed to the professional and fair treatment of consumers.</p>
  <div class="footer-divider" style="left:333px"></div>

  <h4 style="left:360px;top:22px">CONTACT US</h4>
  <ul class="contact-list">
    <li style="height:50px">
      <svg width="8" height="11" viewBox="0 0 8 11" fill="#fff"><path d="M4 0a4 4 0 0 0-4 4c0 3 4 7 4 7s4-4 4-7a4 4 0 0 0-4-4zm0 5.5a1.5 1.5 0 1 1 0-3 1.5 1.5 0 0 1 0 3z"/></svg>
      <span class="org">TOLVANE</span><br>
      <span style="line-height:15px">123 , Lorem Ipsm, Lorem Ipsm,<br>Lorem Ipsm - 123 456</span>
    </li>
    <li style="height:25px;padding-top:4px">
      <svg width="11" height="8" viewBox="0 0 11 8" fill="#fff" style="top:5px"><path d="M0 0h11v8H0z"/><path d="M0 0l5.5 4L11 0" stroke="#0f1419" fill="none"/></svg>
      info@domainname.com
    </li>
    <li style="padding-top:4px">
      <svg width="10" height="10" viewBox="0 0 10 10" fill="#fff" style="top:5px"><rect width="10" height="10" rx="2"/><path d="M3 2l1 2-1 1c.5 1 1 1.5 2 2l1-1 2 1-.5 1.5C4 8 2 6 1.5 2.5z" fill="#0f1419"/></svg>
      123 456 789 000
    </li>
  </ul>
  <div class="footer-divider" style="left:520px"></div>

  <h4 style="left:546px;top:20px">INFORMATION</h4>
  <ul class="info-links">
    <li>About Us</li><li>Services</li><li>Privacy Policy</li><li>Site Map</li><li>Contact Us</li>
  </ul>
  <div class="footer-divider" style="left:650px"></div>

  <div class="badge-a" role="img" aria-label="Industry association membership badge"></div>
  <div class="badge-b" role="img" aria-label="Business accreditation badge"></div>
</footer>

<div class="footer-bottom">
  <p class="copyright">Copyright@2016 Tolvane. All Right Reserved.</p>
  <div class="social" aria-label="Social links"><span></span><span></span><span></span></div>
</div>

</body>
</html>
```